Ridgeline Journeys business card

please see website
www.ridgelinejourneys.comau

info needed on card
Curtis Halvey
Ph
email
Adventure Riding GPS trails

please use my logo and colours off my site

Curtis Halvey
curtis@ridgelinejourneys.com

```html
<!DOCTYPE html>
<html lang="en">
<head>
<meta charset="utf-8">
<title>Ridgeline Journeys – Business Card</title>
<link rel="stylesheet" href="https://fonts.googleapis.com/css2?family=Open+Sans:ital,wght@0,400;0,600;0,700;1,700&display=swap">
<style>
  :root {
    --page-bg: #d9d5d0;
    --card-bg: #ecebe8;
    --panel-dark: #3a3a3c;
    --panel-mid: #5c5c5f;
    --accent-amber: #f2b01e;
    --accent-yellow: #f3dc2a;
    --ink: #1c1c1c;
    --ink-soft: #2a2a2a;
  }
  * { margin: 0; padding: 0; box-sizing: border-box; }
  html, body {
    width: 1200px;
    height: 969px;
    overflow: hidden;
    background: var(--page-bg);
    font-family: "Open Sans", Arial, sans-serif;
  }
  .business-card {
    position: absolute;
    left: 100px;
    top: 200px;
    width: 1000px;
    height: 568px;
    background: var(--card-bg);
    overflow: hidden;
    box-shadow: 0 18px 40px rgba(0,0,0,0.18);
  }
  .decor-panel {
    position: absolute;
    left: 0;
    top: 0;
    width: 255px;
    height: 100%;
    background: linear-gradient(180deg, var(--panel-dark) 0%, var(--panel-mid) 55%, var(--accent-amber) 100%);
  }
  .brand {
    position: absolute;
    left: 500px;
    top: 120px;
    display: flex;
    align-items: center;
    gap: 22px;
  }
  .brand-dot {
    width: 70px;
    height: 70px;
    border-radius: 50%;
    background: var(--accent-amber);
  }
  .brand-name {
    font-weight: 700;
    font-size: 40px;
    line-height: 1;
    color: var(--ink);
    letter-spacing: 0.5px;
  }
  .contact {
    position: absolute;
    right: 55px;
    top: 282px;
    text-align: right;
    color: var(--ink-soft);
  }
  .contact-name {
    font-weight: 600;
    font-size: 36px;
    color: var(--ink);
    line-height: 1.2;
    margin-bottom: 14px;
  }
  .contact-line {
    font-size: 23px;
    line-height: 40px;
  }
  .tagline {
    font-weight: 700;
    font-style: italic;
    font-size: 25px;
    color: var(--ink);
    margin-top: 12px;
  }
</style>
</head>
<body>
  <main class="business-card">
    <div class="decor-panel" role="img" aria-label="Decorative brand panel in charcoal and amber"></div>

    <div class="brand">
      <span class="brand-dot"></span>
      <span class="brand-name">Ridgeline Journeys</span>
    </div>

    <div class="contact">
      <p class="contact-name">Curtis Halvey</p>
      <p class="contact-line">Ph : 612 555 0148</p>
      <p class="contact-line">curtis@ridgelinejourneys.com</p>
      <p class="contact-line">www.ridgelinejourneys.comau</p>
      <p class="tagline">Adventure Riding GPS trails</p>
    </div>
  </main>
</body>
</html>
```